13 Varno - new website design project

Our company Varno Electrical is developing a new lead generation website focused on Electrical, LED Lighting and Solar Power. We need a high converting website.

Example of our current website is www.varnoelectrical-example.com.au You can take content from this website for this new design. Our colours are red, black and white. For our new website we would like to promote Varno, Spark Every Day. Please listen to the jingle.

The below link is the company jingle that we have developed.
http://www.tunecraftdemo.com.au/vrn-tc-v1/

The key for this brief is to generate leads for Electrical, LED Lighting (for commercial) and Solar Power & Storage.

Target Market(s)

Business owners in Melbourne Victoria

Number of Pages Required

4 page

Colors
ec1f27
ffffff

Requirements
Must have
• This page must be clean, be in line with company branding and a high converting lead website.

```html
<!DOCTYPE html>
<html lang="en">
<head>
<meta charset="utf-8">
<title>Varno Electrical</title>
<link rel="stylesheet" href="https://fonts.googleapis.com/css2?family=Open+Sans:wght@400;600;700&family=Oswald:wght@300;400&display=swap">
<style>
:root{
  --red:#ec1f27;
  --ink:#222222;
  --text:#555555;
  --muted:#8a8a8a;
  --light:#eeeeee;
  --tile:#f3f3f3;
  --tile-line:#dddddd;
  --white:#ffffff;
}
*{box-sizing:border-box;margin:0;padding:0}
html,body{width:1200px;height:3046px;overflow:hidden}
body{font-family:"Open Sans",Arial,sans-serif;color:var(--text);background:var(--white);position:relative}

.topbar{position:absolute;top:0;left:0;width:1200px;height:33px;background:var(--light);font-size:13px;color:var(--ink)}
.topbar .contact{position:absolute;left:91px;top:8px;display:flex;gap:18px;align-items:center}
.topbar .contact svg{vertical-align:-2px;margin-right:4px}
.topbar .social{position:absolute;right:91px;top:8px;display:flex;gap:6px}
.topbar .social span{width:16px;height:16px;background:#444;border-radius:2px;display:block}

.header{position:absolute;top:33px;left:0;width:1200px;height:101px;background:var(--white)}
.logo{position:absolute;left:91px;top:22px;display:flex;align-items:center;gap:8px;color:var(--red);font-weight:700}
.logo .mark{width:34px;height:34px;border-radius:50%;background:var(--red)}
.logo .name{font-size:34px;line-height:1}
.logo .tag{position:absolute;left:42px;top:44px;font-size:11px;white-space:nowrap}
.nav{position:absolute;right:91px;top:36px;display:flex;gap:26px;font-size:16px;color:var(--ink)}
.nav a{color:inherit;text-decoration:none;padding:4px 0;border:1px solid transparent;border-radius:16px;white-space:nowrap}
.nav a.active{color:var(--red);border-color:var(--red);padding:4px 16px}

.hero{position:absolute;top:134px;left:0;width:1200px;height:528px;background:linear-gradient(90deg,#3b3d3a 0%,#6a6c68 28%,#9aa09c 55%,#c9cccb 80%,#aeb2b2 100%)}
.hero .dot{position:absolute;top:432px;width:26px;height:26px;border-radius:50%;background:rgba(255,255,255,.5)}
.hero-title{position:absolute;left:648px;top:400px;color:var(--white);font-family:"Oswald",sans-serif;font-size:39px;font-weight:400;line-height:1;white-space:nowrap}
.hero-sub{position:absolute;left:648px;top:449px;color:var(--white);font-family:"Oswald",sans-serif;font-weight:300;font-size:27px;opacity:.9;white-space:nowrap}

.welcome-title{position:absolute;top:705px;left:0;width:1200px;text-align:center;font-weight:400;font-size:31px;color:var(--ink);letter-spacing:.5px}
.welcome-intro{position:absolute;top:756px;left:150px;width:900px;text-align:center;font-size:14.5px;line-height:24px;color:var(--muted)}
.service{position:absolute;top:870px;width:300px;text-align:center}
.service .pic{width:180px;height:180px;margin:0 auto;border-radius:50%;border:5px solid #f2f2f2;box-shadow:0 0 0 1px #ddd}
.service h3{margin-top:24px;font-weight:400;font-size:20px;color:var(--ink)}
.service p{margin-top:10px;font-size:13.5px;line-height:20px;color:var(--muted);padding:0 18px}
.service .more{display:block;margin-top:12px;font-size:14px;color:var(--red)}

.about{position:absolute;top:1248px;left:0;width:1200px;height:413px;background:linear-gradient(100deg,#b61b24 0%,#d0232c 45%,#c21f28 100%)}
.about h2{position:absolute;left:89px;top:102px;color:var(--white);font-weight:400;font-size:28px}
.about p{position:absolute;left:89px;top:148px;width:486px;color:var(--white);font-size:14px;line-height:26px;text-align:justify}
.about .btn{position:absolute;left:89px;top:288px;padding:5px 22px;border:1px solid var(--white);border-radius:16px;color:var(--white);font-size:14px}
.video{position:absolute;left:617px;top:59px;width:496px;height:289px;border:5px solid var(--white);background:linear-gradient(180deg,#9fb4c7 0%,#8a8c8a 45%,#d9d9d9 75%,#f2f2f2 100%)}
.video .play{position:absolute;left:213px;top:110px}

.why-title{position:absolute;top:1724px;left:0;width:1200px;text-align:center;font-weight:400;font-size:28px;color:var(--ink)}
.chev{position:absolute;top:1895px}
.reason{position:absolute;width:440px}
.reason .num{position:absolute;left:0;top:0;width:68px;height:68px;border-radius:50%;border:2px solid #d0d0d0;color:var(--red);font-size:36px;text-align:center;line-height:64px}
.reason h4{margin-left:84px;font-weight:400;font-size:17px;color:var(--ink);letter-spacing:.3px}
.reason p{margin-left:84px;margin-top:6px;font-size:13px;line-height:21px;color:var(--muted)}

.testimonials{position:absolute;top:2108px;left:0;width:1200px;height:349px;background:var(--light)}
.testimonials h2{position:absolute;top:40px;left:0;width:1200px;text-align:center;font-weight:400;font-size:28px;color:var(--ink)}
.quote{position:absolute;top:121px;width:510px}
.quote .pic{position:absolute;left:0;top:0;width:159px;height:142px;border:3px solid var(--white);background:linear-gradient(180deg,#cfcfcf 0%,#9a9fa6 40%,#5f6670 100%)}
.quote p{margin-left:178px;font-size:12.5px;line-height:19px;color:#666}
.quote .who{margin-left:178px;margin-top:8px;font-size:12.5px;line-height:18px;color:var(--red)}
.dots{position:absolute;top:318px;left:583px;display:flex;gap:5px}
.dots span{width:8px;height:8px;border-radius:50%;background:#888}
.dots span.on{background:var(--red)}

.clients-title{position:absolute;top:2518px;left:0;width:1200px;text-align:center;font-weight:400;font-size:28px;color:var(--ink);letter-spacing:.5px}
.client{position:absolute;top:2595px;width:160px;height:91px;display:flex;align-items:center;justify-content:center;background:var(--tile);border:1px solid var(--tile-line);color:#444;font-weight:600;font-size:17px;text-align:center;line-height:1.2}

.footer{position:absolute;top:2753px;left:0;width:1200px;height:293px;background:linear-gradient(180deg,#1c1c1c,#111)}
.footer h5{font-weight:400;font-size:17px;color:var(--white);letter-spacing:.5px}
.fcol{position:absolute;top:56px;color:#ddd}
.fcol p{font-size:12.5px;line-height:19px;margin-top:16px}
.fline{display:flex;align-items:center;gap:12px;margin-top:10px;font-size:13px;white-space:nowrap}
.subscribe{display:flex;margin-top:16px}
.subscribe .field{width:160px;height:40px;background:var(--white);font-size:11px;color:#999;padding:0 12px;line-height:40px;white-space:nowrap}
.subscribe .go{width:80px;height:40px;background:var(--red);color:var(--white);font-size:15px;text-align:center;line-height:40px}
.fsocial{display:flex;gap:16px;margin-top:22px}
.fsocial span{width:34px;height:34px;background:var(--white);border-radius:4px;display:block}
.footer .rule{position:absolute;left:85px;top:232px;width:1030px;height:1px;background:#444}
.footer .copy{position:absolute;top:248px;left:0;width:1200px;text-align:center;font-size:13px;color:#ddd}
</style>
</head>
<body>

<div class="topbar">
  <div class="contact">
    <span><svg width="12" height="12" viewBox="0 0 24 24"><circle cx="12" cy="12" r="12" fill="#ec1f27"/><path d="M8 6l2 0 1 3-1.5 1a7 7 0 0 0 4 4l1-1.5 3 1v2a2 2 0 0 1-2 2A11 11 0 0 1 6 8a2 2 0 0 1 2-2z" fill="#fff"/></svg>: 138 274</span>
    <span><svg width="12" height="10" viewBox="0 0 24 18"><rect width="24" height="18" rx="2" fill="#ec1f27"/><path d="M2 3l10 7 10-7" stroke="#fff" stroke-width="2" fill="none"/></svg>: service@varnoelectrical-example.com.au</span>
  </div>
  <div class="social"><span></span><span></span><span></span><span></span></div>
</div>

<header class="header">
  <div class="logo"><span class="mark"></span><span class="name">VARNO</span><span class="tag">Spark Every Day</span></div>
  <nav class="nav">
    <a class="active">HOME</a><a>VARNO STORY</a><a>OUR WORK</a><a>ELECTRICAL</a><a>LED LIGHTING</a><a>SOLAR POWER</a><a>CONTACT US</a>
  </nav>
</header>

<section class="hero" role="img" aria-label="Electrician in a cap installing a wall-mounted solar inverter beside a house">
  <span class="dot" style="left:84px"></span>
  <span class="dot" style="left:110px;background:rgba(255,255,255,.25)"></span>
  <div class="hero-title">VARNO ELECTRICAL IS DEVELOPING</div>
  <div class="hero-sub">Electrical, LED Lighting and Solar Power</div>
</section>

<section class="welcome">
  <h1 class="welcome-title">WELCOME TO VARNO ELECTRICAL</h1>
  <p class="welcome-intro">Electrical and Energy Solutions are at the forefront of our company. Varno Electrical has a long history in Electrical, LED Lighting and Solar Power and just like the Cougar, we will strive to be fierce &amp; agile in an effort to exceed our customer's expectations and develop stronger links with all our business partners &amp; community</p>
  <div class="service" style="left:150px">
    <div class="pic" role="img" aria-label="Electrician working on a switchboard" style="background:radial-gradient(circle,#c9a27a,#5b5048 70%)"></div>
    <h3>ELECTRICAL</h3>
    <p>Varno Electrical was formed to be an expert Electricity Contracting Company providing services to all Residential and Commercial</p>
    <span class="more">Read More -&gt;</span>
  </div>
  <div class="service" style="left:450px">
    <div class="pic" role="img" aria-label="LED flood light fitting" style="background:radial-gradient(circle,#d6d6d6,#3a3a3a 75%)"></div>
    <h3>LED LIGHTING</h3>
    <p>Varno Electrical was formed to be an expert Electricity Contracting Company providing services to all Residential and Commercial</p>
    <span class="more">Read More -&gt;</span>
  </div>
  <div class="service" style="left:750px">
    <div class="pic" role="img" aria-label="Solar inverter and storage unit" style="background:radial-gradient(circle,#f4f4f6,#6b8bb0 80%)"></div>
    <h3>SOLAR POWER</h3>
    <p>Varno Electrical was formed to be an expert Electricity Contracting Company providing services to all Residential and Commercial</p>
    <span class="more">Read More -&gt;</span>
  </div>
</section>

<section class="about">
  <h2>ABOUT US</h2>
  <p>Electrical and Energy Solutions are at the forefront of our company. Varno Electrical has a long history in Electrical, LED Lighting and Solar Power and just like the Cougar, we will strive to be fierce &amp; agile in an effort to exceed our customer's expectations and develop stronger links with all our business partners &amp; community.</p>
  <span class="btn">Read More</span>
  <div class="video" role="img" aria-label="Video still of installers on a roof with a company van below">
    <svg class="play" width="66" height="66" viewBox="0 0 66 66"><circle cx="33" cy="33" r="33" fill="rgba(0,0,0,.55)"/><path d="M26 20l20 13-20 13z" fill="#fff"/></svg>
  </div>
</section>

<section class="why">
  <h2 class="why-title">WHY CHOOSE US?</h2>
  <svg class="chev" style="left:42px" width="18" height="34" viewBox="0 0 18 34"><path d="M16 2L2 17l14 15" stroke="#bbb" stroke-width="2" fill="none"/></svg>
  <svg class="chev" style="left:1140px" width="18" height="34" viewBox="0 0 18 34"><path d="M2 2l14 15L2 32" stroke="#bbb" stroke-width="2" fill="none"/></svg>
  <div class="reason" style="left:103px;top:1813px"><span class="num">1</span><h4>PROFESSIONAL SERVICE</h4><p>When you hire a Varno Electrical Electrician you will get a professional and well-presented Electrician that comes skilled and ready to do the job.</p></div>
  <div class="reason" style="left:640px;top:1813px"><span class="num">2</span><h4>5 YEAR WORKMANSHIP GUARANTEE</h4><p>You can buy with confidence as all of our work has a 5 year workmanship guarantee. For your peace of mind, we unconditionally back our electrical work. We will come back to fix any problems</p></div>
  <div class="reason" style="left:103px;top:1935px"><span class="num">3</span><h4>VALUE FOR MONEY</h4><p>We provide extremely competitive pricing, which means you get value for money on quality that is comparable to the best in the industry.</p></div>
  <div class="reason" style="left:640px;top:1935px"><span class="num">4</span><h4>ENVIRONMENTALLY FRIENDLY</h4><p>We a committed to reducing carbon emissions by installing Solar Power and upgrading sites to LED Lighting. In addition to reducing the carbon emissions we recycle Fluorescent Tubes.</p></div>
</section>

<section class="testimonials">
  <h2>TESTIMONIAL</h2>
  <div class="quote" style="left:91px">
    <div class="pic" role="img" aria-label="Client retail store interior"></div>
    <p>The service, communication and after sales service of Varno Electrical has been awesome. We would strongly recommend them to any business contemplating upgrading their lighting or any other electrical work.</p>
    <div class="who">Jordan Pellow<br>Executive Marlow Trading</div>
  </div>
  <div class="quote" style="left:627px">
    <div class="pic" role="img" aria-label="Client shop interior with bright lighting"></div>
    <p>They clean up after the job, explained everything I needed to know and answered all questions, very professional. Will use them again in the future!</p>
    <div class="who">R. Dunmore<br>Kew East VIC</div>
  </div>
  <div class="dots"><span class="on"></span><span></span><span></span></div>
</section>

<section class="clients">
  <h2 class="clients-title">OUR SATISFIED CLIENTS INCLUDE...</h2>
  <div class="client" style="left:255px">Corvale Retail</div>
  <div class="client" style="left:445px">Marlow Trading</div>
  <div class="client" style="left:637px">Brightpath Fittings</div>
  <div class="client" style="left:829px">Tidewell Foods</div>
</section>

<footer class="footer">
  <div class="fcol" style="left:85px">
    <h5>CONTACT US</h5>
    <p>12/48 HALLAM RD<br>GLEN IRIS VIC 3146</p>
    <div class="fline"><svg width="16" height="16" viewBox="0 0 24 24"><path d="M6 2l4 0 2 5-2.5 1.5a11 11 0 0 0 6 6L17 12l5 2v4a2 2 0 0 1-2 2A18 18 0 0 1 4 4a2 2 0 0 1 2-2z" fill="none" stroke="#ddd" stroke-width="1.6"/></svg><span style="font-size:17px">138 274</span></div>
    <div class="fline"><svg width="16" height="12" viewBox="0 0 24 18"><rect x="1" y="1" width="22" height="16" fill="none" stroke="#ddd" stroke-width="1.6"/><path d="M1 1l11 8 11-8" stroke="#ddd" stroke-width="1.6" fill="none"/></svg><span>service@varnoelectrical-example.com.au</span></div>
  </div>
  <div class="fcol" style="left:386px;width:245px">
    <h5>VARNOELECTRICAL</h5>
    <p style="text-align:justify">Varno Electrical was formed to be an expert Electricity Contracting Company providing services to all Residential and Commercial Customers. With over 10 years of experience, Varno Electrical has developed a highly-experienced</p>
  </div>
  <div class="fcol" style="left:670px;width:250px">
    <h5>NEWSLETTER</h5>
    <p>Excepteur sint occaecat cupidatat non proident, sunt in culpa qui officia deserunt mollit anim</p>
    <div class="subscribe"><div class="field">Enter your email address</div><div class="go">Sign Up</div></div>
  </div>
  <div class="fcol" style="left:972px">
    <h5>SOCIAL MEDIA</h5>
    <div class="fsocial"><span></span><span></span><span></span></div>
  </div>
  <div class="rule"></div>
  <div class="copy">Copyright © 2017. All Rights Reserved</div>
</footer>

</body>
</html>
```